Online-Marketing-Material für Reinigungsbetrieb
Zielgruppe
Wir sind ein Reinigungsbetrieb mit den Schwerpunkten Treppenhausreinigung und Büroreinigung. Die Zielgruppe sind bei dieser Anzeige Unternehmer.
Aufgabenstellung
Wir wollen eine Aktion starten. 20 Prozent Neukundenrabatt auf Büroreinigungen. Wir sind ein junges, modernes Unternehmen, dass so auch dementsprechend rüber kommen soll.
Gerne mit unseren Farben.

```html
<!DOCTYPE html>
<html lang="de">
<head>
<meta charset="utf-8">
<title>Lindhof Clean – Neukundenrabatt</title>
<link href="https://fonts.googleapis.com/css2?family=Bebas+Neue&family=Lato:ital,wght@0,400;0,700;1,400&display=swap" rel="stylesheet">
<style>
  :root {
    --blue: #2f6fba;
    --blue-deep: #1f5aa6;
    --ink: #2e3a94;
    --yellow: #fdc80f;
    --white: #ffffff;
    --teal: #3cb7c4;
    --glove-pink: #f29cc4;
    --glove-yellow: #fde93a;
    --glove-orange: #f7942e;
    --glove-blue: #55b3e6;
  }
  * { margin: 0; padding: 0; box-sizing: border-box; }
  html, body { width: 855px; height: 1200px; overflow: hidden; background: var(--blue); }
  .flyer { position: relative; width: 855px; height: 1200px; overflow: hidden; font-family: 'Lato', sans-serif; }
  .shapes { position: absolute; inset: 0; }
  .promo-tag {
    position: absolute; left: 546px; top: 40px; width: 248px; text-align: center;
    font-family: 'Bebas Neue', sans-serif; font-size: 42px; color: var(--ink); letter-spacing: 0.5px;
  }
  .brand { position: absolute; left: 60px; top: 530px; display: flex; align-items: center; gap: 12px; }
  .brand-mark { width: 70px; height: 70px; background: var(--ink); }
  .brand-name { font-weight: 700; font-size: 24px; line-height: 25px; color: var(--ink); }
  .brand-owner { font-size: 9px; color: var(--teal); margin-top: 3px; }
  .headline {
    position: absolute; left: 0; width: 855px; top: 666px; text-align: center;
    font-family: 'Bebas Neue', sans-serif; font-size: 110px; line-height: 1; color: var(--white); letter-spacing: 1px;
  }
  .subline {
    position: absolute; left: 0; width: 855px; top: 776px; text-align: center;
    font-family: 'Bebas Neue', sans-serif; font-size: 56px; line-height: 1; color: var(--yellow); letter-spacing: 2px;
  }
  .rule { position: absolute; left: 88px; width: 676px; height: 3px; background: var(--white); border-radius: 2px; }
  .rule.top { top: 838px; }
  .rule.bottom { top: 898px; }
  .tagline {
    position: absolute; left: 0; width: 855px; top: 853px; text-align: center;
    font-size: 28px; line-height: 34px; color: var(--white);
  }
  .service { position: absolute; top: 926px; width: 180px; text-align: center; }
  .service-photo {
    width: 134px; height: 134px; margin: 0 auto; border-radius: 50%; border: 6px solid var(--blue-deep);
    background: linear-gradient(150deg, #dfe6ee, #8ea6c2);
  }
  .service-photo.accent { border-color: var(--yellow); }
  .service-label { margin-top: 12px; font-style: italic; font-size: 15.5px; color: var(--white); }
  .contact-bar { position: absolute; left: 0; top: 1106px; width: 855px; height: 47px; background: var(--yellow); }
  .contact { position: absolute; top: 15px; display: flex; align-items: center; gap: 9px; font-size: 12.5px; color: var(--ink); }
  .contact svg { width: 14px; height: 14px; flex: none; }
</style>
</head>
<body>
<div class="flyer">
  <svg class="shapes" width="855" height="1200" viewBox="0 0 855 1200">
    <defs>
      <linearGradient id="sky" x1="0" y1="0" x2="0" y2="1">
        <stop offset="0" stop-color="#4f93d3"/>
        <stop offset="1" stop-color="#eef5fc"/>
      </linearGradient>
      <linearGradient id="gloves" x1="0" y1="0" x2="1" y2="0">
        <stop offset="0" stop-color="var(--glove-pink)"/>
        <stop offset="0.2" stop-color="var(--glove-pink)"/>
        <stop offset="0.3" stop-color="var(--glove-yellow)"/>
        <stop offset="0.44" stop-color="var(--glove-yellow)"/>
        <stop offset="0.52" stop-color="var(--glove-orange)"/>
        <stop offset="0.68" stop-color="var(--glove-orange)"/>
        <stop offset="0.76" stop-color="var(--glove-blue)"/>
        <stop offset="1" stop-color="var(--glove-blue)"/>
      </linearGradient>
      <linearGradient id="glovesFade" x1="0" y1="0" x2="0" y2="1">
        <stop offset="0" stop-color="#fff" stop-opacity="1"/>
        <stop offset="0.8" stop-color="#fff" stop-opacity="1"/>
        <stop offset="1" stop-color="#fff" stop-opacity="0"/>
      </linearGradient>
      <mask id="glovesMask"><rect x="0" y="70" width="855" height="460" fill="url(#glovesFade)"/></mask>
    </defs>
    <g role="img" aria-label="Foto: bunte Gummihandschuhe in Rosa, Gelb, Orange und Blau hängen nebeneinander vor hellem Himmel">
      <rect x="0" y="0" width="855" height="700" fill="url(#sky)"/>
      <rect x="0" y="70" width="855" height="460" fill="url(#gloves)" mask="url(#glovesMask)"/>
    </g>
    <polygon points="546,0 794,0 794,84 670,134 546,84" fill="var(--yellow)"/>
    <polygon points="0,350 300,584 0,674" fill="var(--yellow)"/>
    <polygon points="0,674 553,510 855,642 855,1200 0,1200" fill="var(--blue)"/>
    <g fill="var(--yellow)">
      <polygon points="484,577 487,584 494,584 488,589 490,596 484,592 478,596 480,589 474,584 481,584"/>
      <polygon points="548,549 553,560 565,560 555,567 559,579 548,572 537,579 541,567 531,560 543,560"/>
      <polygon points="529,591 535,604 549,604 538,612 542,626 529,618 516,626 520,612 509,604 523,604"/>
    </g>
  </svg>

  <div class="promo-tag">Aktion 20%</div>

  <div class="brand">
    <div class="brand-mark"></div>
    <div>
      <div class="brand-name">Lindhof<br>Clean</div>
      <div class="brand-owner">Inh. Jonas Brenner</div>
    </div>
  </div>

  <h1 class="headline">Neukundenrabatt</h1>
  <h2 class="subline">Auf alle Büroreinigungen</h2>
  <div class="rule top"></div>
  <p class="tagline">SCHENKEN SIE IHREM OBJEKT NEUEN GLANZ</p>
  <div class="rule bottom"></div>

  <div class="service" style="left:66px">
    <div class="service-photo" role="img" aria-label="Foto: Wischmopp und Eimer in einem Büro"></div>
    <p class="service-label">Büro Reinigungen</p>
  </div>
  <div class="service" style="left:247px">
    <div class="service-photo accent" role="img" aria-label="Foto: gelbes Warnschild Rutschgefahr auf nassem Boden" style="background:linear-gradient(150deg,#f3c81a,#5a5a5a)"></div>
    <p class="service-label">Treppenhäuser</p>
  </div>
  <div class="service" style="left:426px">
    <div class="service-photo" role="img" aria-label="Foto: professionelles Reinigungsgerät" style="background:linear-gradient(150deg,#d9dde2,#6b6f75)"></div>
    <p class="service-label">Professionell</p>
  </div>
  <div class="service" style="left:606px">
    <div class="service-photo accent" role="img" aria-label="Foto: Hand im Handschuh mit Sprühflasche" style="background:linear-gradient(150deg,#eef4fa,#8fb3da)"></div>
    <p class="service-label">Garantierte Zufriedenheit</p>
  </div>

  <div class="contact-bar">
    <div class="contact" style="left:121px">
      <svg viewBox="0 0 24 24" fill="var(--ink)"><path d="M6.6 10.8a15.1 15.1 0 0 0 6.6 6.6l2.2-2.2a1 1 0 0 1 1-.25 11.4 11.4 0 0 0 3.6.57 1 1 0 0 1 1 1V20a1 1 0 0 1-1 1A17 17 0 0 1 3 4a1 1 0 0 1 1-1h3.5a1 1 0 0 1 1 1c0 1.25.2 2.45.57 3.57a1 1 0 0 1-.25 1z"/></svg>
      <span>+49-555-0100-200</span>
    </div>
    <div class="contact" style="left:275px">
      <svg viewBox="0 0 24 24" fill="none" stroke="var(--ink)" stroke-width="2.4"><rect x="6" y="2" width="12" height="20" rx="2"/><line x1="11" y1="18" x2="13" y2="18"/></svg>
      <span>+49-555-0100-211</span>
    </div>
    <div class="contact" style="left:426px">
      <svg viewBox="0 0 24 24" fill="none" stroke="var(--ink)" stroke-width="2.4"><circle cx="12" cy="12" r="4"/><path d="M16 8v5a3 3 0 0 0 6 0v-1a10 10 0 1 0-4 8"/></svg>
      <span>info@lindhofclean.de</span>
    </div>
    <div class="contact" style="left:617px">
      <svg viewBox="0 0 24 24" fill="none" stroke="var(--ink)" stroke-width="1.8"><circle cx="12" cy="12" r="10"/><ellipse cx="12" cy="12" rx="4.5" ry="10"/><line x1="2" y1="12" x2="22" y2="12"/><path d="M4 7h16M4 17h16"/></svg>
      <span>www.lindhofclean.de</span>
    </div>
  </div>
</div>
</body>
</html>
```